BRAMBLEFORD CONSTRUCTIONS B-Card

I currently have a b-card design but will be removing the image (tree) from the logo and have text only.
I want the card to be classy and strong within the building and construction industry.
I will be using Spot UV on the cards as per the attached examples. I will also send through some sketched ideas that I have in mind.
The color blue is similar to the image (No. 6) attached images

Target Market(s)

middle to maturre aged.
Home Owners / Renovators and Builders

Industry/Entity Type

Construction

Contact Information for Business Card

BRAMBLEFORD CONSTRUCTIONS
Name: Gareth Pennick
Title: Project Manager
Mobile: 0427 351 804
Office: (08) 9316 5172
Address: 47C Corvell Street, Malaga WA 6090
Email: info@bramblefordhomes.com.au
PO Box: 3817 Malaga WA 6944

Colors
0592cd
33a6d7
85cae6
1b1b1b

Requirements
Must have
• 1. It must have spot UV on the front of card, maybe back of card too
• 2. I really like the blue on image 6. (or at least a really cool electric blue against the charcoal grey background)
• 3. The font must be slimline and modern. Easy to read
• 4. There must be no black used on the card... Only greys and dark charcoal greys
• 5. Use only the text from the logo "Brambleford Constructions" Not the image of the tree. I am wanting the b-cards to be more masculine.
Nice to have
• 1. I like the design concept on image 6. but happy to see what else you can do with the Spot UV
• 2. Unless you have a really cool idea of the image of the tree (from previous logo) Spot UV somewhere in the design concept thats original and different then I am keen to see what you come up with
• 3. Try changing the color of the logo eg. full white or Blue and white
• 4. Another option is to have the Brambleford Logo on the front of card with the spot UV in the background of text which we specialise in eg, Roofing, Ceiling, Insulation, Gutter Guards, Electrical, Insurance etc and we can add or reduce items as required. Similar to image 12.
Should not have
• Do not include the image of the tree from previous logo. unless you have a really cool idea of Spot UV somewhere in the design concept thats original and different.

```html
<!DOCTYPE html>
<html lang="en">
<head>
<meta charset="utf-8">
<title>Brambleford Constructions – Business Card</title>
<link href="https://fonts.googleapis.com/css2?family=Mulish:wght@400;600;700;800&display=swap" rel="stylesheet">
<style>
  :root {
    --bg: #e7e5e1;
    --brand-blue: #1f5fae;
    --card-white: #ffffff;
    --charcoal: #2b2b2b;
    --text-grey: #4a4a4a;
    --rule-grey: #c9c9c9;
  }
  * { box-sizing: border-box; margin: 0; padding: 0; }
  html, body { width: 1200px; height: 843px; overflow: hidden; }
  body {
    background: var(--bg);
    font-family: "Mulish", sans-serif;
    display: flex;
    flex-direction: column;
    align-items: center;
    justify-content: center;
    gap: 56px;
  }
  .card {
    position: relative;
    width: 560px;
    height: 342px;
    border-radius: 2px;
    box-shadow: 0 6px 18px rgba(0,0,0,0.18);
    overflow: hidden;
  }

  /* Back side */
  .card--back {
    background: var(--brand-blue);
    color: #fff;
    display: flex;
    flex-direction: column;
    align-items: center;
    justify-content: center;
  }
  .wordmark {
    text-align: center;
    font-weight: 800;
    line-height: 1;
    white-space: nowrap;
  }
  .wordmark__name { font-size: 46px; letter-spacing: 0.5px; }
  .wordmark__sub { font-size: 14px; letter-spacing: 9px; margin-top: 4px; padding-left: 9px; }
  .card--back .wordmark { color: #fff; }
  .services {
    margin-top: 26px;
    font-size: 15px;
    font-weight: 400;
    text-align: center;
    line-height: 1.45;
  }

  /* Front side */
  .card--front { background: var(--card-white); }
  .card--front .wordmark {
    position: absolute;
    left: 28px;
    top: 92px;
    width: 246px;
    color: var(--brand-blue);
  }
  .card--front .wordmark__name { font-size: 29px; letter-spacing: 0; }
  .card--front .wordmark__sub { font-size: 10px; letter-spacing: 6.4px; padding-left: 6px; margin-top: 3px; color: var(--charcoal); }
  .divider {
    position: absolute;
    left: 292px;
    top: 40px;
    width: 1px;
    height: 190px;
    background: var(--rule-grey);
  }
  .contact {
    position: absolute;
    left: 312px;
    top: 46px;
    color: var(--text-grey);
  }
  .contact__name { color: var(--brand-blue); font-size: 22px; font-weight: 700; }
  .contact__title { color: var(--charcoal); font-size: 13px; font-weight: 600; margin-bottom: 8px; }
  .contact__address { font-size: 12.5px; line-height: 1.35; margin-bottom: 8px; }
  .contact__line {
    display: flex;
    align-items: center;
    gap: 8px;
    font-size: 13px;
    line-height: 1.5;
  }
  .contact__line svg { width: 13px; height: 13px; flex: none; fill: var(--brand-blue); }
  .swoosh { position: absolute; left: 0; top: 0; }
</style>
</head>
<body>

  <section class="card card--back">
    <div class="wordmark">
      <div class="wordmark__name">BRAMBLEFORD</div>
      <div class="wordmark__sub">CONSTRUCTIONS</div>
    </div>
    <p class="services">
      Roofing &bull; Ceiling &bull; Insulation &bull; Gutter Guards<br>
      Electrical &bull; Insurance etc
    </p>
  </section>

  <section class="card card--front">
    <svg class="swoosh" width="560" height="342" viewBox="0 0 560 342" aria-hidden="true">
      <path d="M0,212 C120,262 300,300 560,322 L560,342 L0,342 Z" fill="var(--brand-blue)"/>
      <path d="M0,198 C120,250 300,290 560,310" fill="none" stroke="var(--charcoal)" stroke-width="5"/>
    </svg>

    <div class="wordmark">
      <div class="wordmark__name">BRAMBLEFORD</div>
      <div class="wordmark__sub">CONSTRUCTIONS</div>
    </div>

    <div class="divider"></div>

    <div class="contact">
      <div class="contact__name">Gareth Pennick</div>
      <div class="contact__title">Project Manager</div>
      <div class="contact__address">
        47C Corvell Street<br>
        Malaga WA 6090<br>
        PO Box: 3817 Malaga<br>
        WA 6944
      </div>
      <div class="contact__line">
        <svg viewBox="0 0 16 16"><path d="M3.6 1.2l2.2 2.6-1.3 1.7c.9 2 2.4 3.5 4.4 4.4l1.7-1.3 2.6 2.2-1.2 2.6C6.6 13.2 2.8 9.4 1 3.1z"/></svg>
        (08) 9316 5172
      </div>
      <div class="contact__line">
        <svg viewBox="0 0 16 16"><path d="M4 0h8a1 1 0 0 1 1 1v14a1 1 0 0 1-1 1H4a1 1 0 0 1-1-1V1a1 1 0 0 1 1-1zm.8 2v10.5h6.4V2zM8 13.3a.9.9 0 1 0 0 1.8.9.9 0 0 0 0-1.8z"/></svg>
        0427 351 804
      </div>
      <div class="contact__line">
        <svg viewBox="0 0 16 16"><path d="M1 3h14v10H1zm1.5 1.5v.3L8 8.6l5.5-3.8v-.3zm0 2.1v4.9h11V6.6L8 10.4z"/></svg>
        info@bramblefordhomes.com.au
      </div>
    </div>
  </section>

</body>
</html>
```